Law Firm in Texas in need of new letterhead

Law Firm in Fort Worth, TX, USA named "Pell & Varnum, Attorneys-At-Law, LLP." This is a general practice law firm that mostly does Family Law and Criminal Defense work.

We are looking for a new letterhead that has a "classical" appeal, with modern elements.

Any color combination is fine, but please note that we do fax many documents, so the design must be clearly legible in Black and White.

We would like our letterhead to project a sense of professionalism, integrity, and ability.

Target Market(s)

Letterhead will be for correspondence generally with other attorneys and clients.

Industry/Entity Type

Law Firm

Logo Text

Pell & Varnum, Attorneys-At-Law, LLP.

Logo styles of interest
Pictorial/Combination Logo
Wordmark Logo
Lettermark Logo
Requirements
Nice to have
• Although not necessary, a "Texas Star" that is incorporated into the design would be a nice touch.
Should not have
• Colors that do not convert to B&W easily

```html
<!DOCTYPE html>
<html lang="en">
<head>
<meta charset="utf-8">
<title>Pell &amp; Varnum Letterhead</title>
<link href="https://fonts.googleapis.com/css2?family=Cinzel:wght@500&family=Montserrat:wght@400;600&display=swap" rel="stylesheet">
<style>
  :root {
    --backdrop: #ebebeb;
    --paper: #f8f8f8;
    --navy: #1d4a73;
    --navy-deep: #17426a;
    --accent-blue: #3b86c2;
    --light-blue: #5aa8e0;
    --ink-grey: #7a7f85;
    --star-grey: #dcdcdc;
    --rule-grey: #9a9a9a;
  }
  * { margin: 0; padding: 0; box-sizing: border-box; }
  html, body { width: 1200px; height: 815px; overflow: hidden; }
  body {
    position: relative;
    background: var(--backdrop);
    font-family: "Montserrat", Arial, sans-serif;
  }
  .sheet {
    position: absolute;
    top: 70px;
    width: 484px;
    height: 685px;
    background: var(--paper);
  }
  .sheet--star { left: 80px; }
  .sheet--classic { left: 638px; }

  .wordmark {
    font-family: "Cinzel", "Times New Roman", serif;
    font-weight: 500;
    color: var(--navy);
    line-height: 1;
    white-space: nowrap;
  }
  .wordmark__name { font-size: 23px; letter-spacing: 0.5px; display: block; }
  .wordmark__tagline { font-size: 12px; letter-spacing: 0.6px; display: block; margin-top: 6px; }

  .sheet--star .wordmark {
    position: absolute; top: 44px; left: 0; width: 100%; text-align: center;
  }
  .star-watermark {
    position: absolute; left: 73px; top: 212px; width: 336px; height: 314px;
    background: radial-gradient(ellipse at center, var(--star-grey) 0%, rgba(220,220,220,0.35) 55%, rgba(248,248,248,0) 72%);
  }

  .footer-band {
    position: absolute; left: 0; bottom: 0; width: 100%; height: 48px;
    background: var(--navy-deep);
    color: #fff; font-size: 5.6px; line-height: 7.6px;
  }
  .footer-band__edge {
    position: absolute; left: 0; top: 0; width: 13px; height: 100%; background: var(--accent-blue);
  }
  .footer-band .block { position: absolute; }
  .footer-band .firm { left: 35px; top: 8px; letter-spacing: 0.2px; }
  .footer-band .address { left: 47px; top: 22px; border-left: 1px solid #fff; padding-left: 0; }
  .footer-band .address span, .footer-band .phones span { display: block; }
  .footer-band .address { border: none; }
  .vbar { position: absolute; width: 1px; background: #c8d6e4; }
  .footer-band .phones { left: 133px; top: 22px; }
  .label { color: var(--light-blue); font-weight: 600; }
  .footer-band .partner-one { left: 228px; top: 8px; }
  .footer-band .partner-two { left: 362px; top: 8px; }
  .footer-band .partner-name { color: var(--light-blue); font-weight: 600; }

  .sheet--classic .mark-square {
    position: absolute; left: 61px; top: 40px; width: 50px; height: 50px;
    background: var(--navy); border: 2px solid var(--navy);
    outline: 1px solid #fff; outline-offset: -5px;
  }
  .sheet--classic .wordmark { position: absolute; left: 124px; top: 47px; }
  .sheet--classic .wordmark__tagline { margin-left: 2px; }

  .contact {
    position: absolute; font-size: 5.6px; line-height: 7px; color: var(--ink-grey);
  }
  .contact span { display: block; }
  .contact .label { color: var(--navy); }
  .contact--address { left: 60px; top: 646px; }
  .contact--phones { left: 129px; top: 646px; }
  .contact--partners { right: 44px; top: 592px; text-align: right; }
  .contact--partners .partner-name { color: #555b61; font-weight: 600; margin-bottom: 1px; }
  .contact--partners .gap { height: 7px; }
</style>
</head>
<body>

  <section class="sheet sheet--star" aria-label="Letterhead with Texas star">
    <header class="wordmark">
      <span class="wordmark__name">Pell &amp; Varnum</span>
      <span class="wordmark__tagline">Attorneys At Law, LLP</span>
    </header>

    <div class="star-watermark" role="img" aria-label="Faint grey Texas star watermark"></div>

    <footer class="footer-band">
      <div class="footer-band__edge"></div>
      <div class="block firm">PELL &amp; VARNUM, ATTORNEYS-AT-LAW, LLP</div>
      <div class="vbar" style="left:35px; top:22px; height:15px;"></div>
      <div class="block address"><span>1420 E. Lancaster Ave.</span><span>Fort Worth, TX 76103</span></div>
      <div class="vbar" style="left:121px; top:22px; height:15px;"></div>
      <div class="block phones"><span><b class="label">Phone:</b> (817) 555-0142</span><span><b class="label">Fax:</b> (817) 555-0187</span></div>
      <div class="vbar" style="left:217px; top:8px; height:30px;"></div>
      <div class="block partner-one">
        <span class="partner-name">DANIEL PELL</span> - Managing Partner<br>
        - Licensed in State of Texas<br>
        - United States District Court<br>
        - United States Supreme Court
      </div>
      <div class="vbar" style="left:350px; top:8px; height:30px;"></div>
      <div class="block partner-two">
        <span class="partner-name">LAURA JEAN VARNUM</span><br>
        - Licensed in the State of Texas
      </div>
    </footer>
  </section>

  <section class="sheet sheet--classic" aria-label="Classic letterhead">
    <div class="mark-square"></div>
    <header class="wordmark">
      <span class="wordmark__name">Pell &amp; Varnum</span>
      <span class="wordmark__tagline">Attorneys At Law, LLP</span>
    </header>

    <div class="contact contact--address"><span>1420 E. Lancaster Ave.</span><span>Fort Worth, TX 76103</span></div>
    <div class="vbar" style="left:122px; top:646px; height:14px; background:var(--rule-grey);"></div>
    <div class="contact contact--phones"><span><b class="label">Phone:</b> (817) 555-0142</span><span><b class="label">Fax:</b> (817) 555-0187</span></div>

    <div class="contact contact--partners">
      <span class="partner-name">DANIEL PELL</span>
      <span>Managing Partner</span>
      <span class="gap"></span>
      <span>- Licensed in State of Texas</span>
      <span>- United States District Court</span>
      <span>- United States Supreme Court</span>
      <span class="gap"></span>
      <span class="partner-name">LAURA JEAN VARNUM</span>
      <span>- Licensed in the State of Texas</span>
    </div>
    <div class="vbar" style="left:449px; top:598px; height:62px; background:var(--rule-grey);"></div>
  </section>

</body>
</html>
```